NEW Modern Sleek Business Card for VR Language Startup

Our startup is using VR to lead the next wave of world language education. We need a two-sided business card that introduces the larger organization (Brightloom Language Inc) and our contact info on one side and shows the product, Glimwoorld, on the other side.

Side 1 (contact info)= Brightloom Logo and Contact info (name, title, phone, email)

Side 2 (product)= Glimworld logo, text, and website
Text= Culturally Immersive Language Learning Games
Website= www.glimworld-play.com

Target Market(s)

Education, Technology

Contact Information for Business Card

Contact info will be updated upon approval of the design. For now, put this as a placeholder.

Perry Dunmore
Founder & CEO
pdunmore@quillpost-mail.net
(555)-014-2286

Font styles to use
Other font styles liked:
• Gibson and Century Gothic are the brand fonts

Requirements
Nice to have
• I would love to see cohesion between the design and colors of the two logos. I have attached a few business card designs that I like, so you can get a feel for my preferred style.

```html
<!DOCTYPE html>
<html lang="en">
<head>
<meta charset="utf-8">
<title>Brightloom Language — Business Card</title>
<link rel="stylesheet" href="https://fonts.googleapis.com/css2?family=Montserrat:wght@500;600;700&family=Questrial&family=Josefin+Sans:wght@600&display=swap">
<style>
  :root {
    --page: #e6e6e6;
    --card: #ffffff;
    --ink: #1c1c1c;
    --ink-soft: #4a4a4a;
    --violet: #6a4cf0;
    --cyan: #22d8ea;
    --blue: #3f8df5;
    --orange: #f2aa3a;
    --red: #fc3340;
    --magenta: #b04aa8;
    --accent-red: #e8322f;
  }
  * { margin: 0; padding: 0; box-sizing: border-box; }
  html, body { width: 1200px; height: 1200px; overflow: hidden; }
  body { background: var(--page); position: relative; font-family: "Questrial", sans-serif; }

  .card {
    position: absolute; top: 261px; width: 392px; height: 677px;
    background: var(--card); border-radius: 32px; overflow: hidden;
    box-shadow: 0 4px 14px rgba(0,0,0,.18);
    text-align: center;
  }
  .card--product { left: 156px; }
  .card--contact { left: 655px; }

  /* product side */
  .brand-dot {
    position: absolute; left: 50%; transform: translateX(-50%);
    border-radius: 50%;
  }
  .card--product .brand-dot {
    top: 200px; width: 130px; height: 130px;
    background: linear-gradient(135deg, var(--cyan), var(--blue) 55%, var(--violet));
  }
  .product-name {
    position: absolute; top: 346px; left: 0; right: 0;
    font-family: "Montserrat", sans-serif; font-weight: 600;
    font-size: 48px; color: var(--ink-soft); letter-spacing: -0.5px;
  }
  .tagline {
    position: absolute; top: 406px; left: 0; right: 0;
    font-size: 15.5px; line-height: 20px; color: var(--violet);
  }
  .website {
    position: absolute; top: 872px; top: 611px; left: 0; right: 0;
    font-family: "Montserrat", sans-serif; font-weight: 700;
    font-size: 14.5px; color: var(--ink-soft);
  }

  /* contact side */
  .card--contact .brand-dot {
    top: 24px; width: 104px; height: 104px;
    background: var(--red);
  }
  .company-name {
    position: absolute; top: 148px; left: 0; right: 0;
    font-family: "Montserrat", sans-serif; font-weight: 700;
    font-size: 34px; letter-spacing: 5px; color: var(--ink);
  }
  .company-sub {
    position: absolute; top: 198px; left: 0; right: 0;
    font-family: "Montserrat", sans-serif; font-weight: 700;
    font-size: 20px; letter-spacing: 12px; color: var(--ink);
    padding-left: 12px;
  }
  .person-name {
    position: absolute; top: 300px; left: 0; right: 0;
    font-family: "Josefin Sans", sans-serif; font-weight: 600;
    font-size: 25px; color: var(--ink);
  }
  .person-title {
    position: absolute; top: 334px; left: 0; right: 0;
    font-size: 14.5px; color: var(--ink);
  }
  .divider {
    position: absolute; top: 371px; left: 175px; width: 42px; height: 1.5px;
    background: var(--accent-red);
  }
  .contact-line {
    position: absolute; left: 0; right: 0;
    display: flex; justify-content: center; align-items: center; gap: 5px;
    font-size: 14.5px; color: var(--ink); letter-spacing: .3px;
  }
  .contact-line--phone { top: 392px; }
  .contact-line--email { top: 421px; }
  .contact-line svg { width: 13px; height: 13px; flex: none; }

  .corner-accent {
    position: absolute; left: 185px; top: 460px; width: 330px; height: 330px;
    border-radius: 50%;
    background: linear-gradient(180deg, var(--orange), var(--red) 55%, var(--magenta));
  }
</style>
</head>
<body>

<section class="card card--product">
  <div class="brand-dot"></div>
  <h1 class="product-name">Glimworld</h1>
  <p class="tagline">Culturally Immersive Language<br>Learning Games</p>
  <p class="website">www.glimworld-play.com</p>
</section>

<section class="card card--contact">
  <div class="brand-dot"></div>
  <h1 class="company-name">BRIGHTLOOM</h1>
  <p class="company-sub">LANGUAGE</p>

  <h2 class="person-name">PERRY DUNMORE</h2>
  <p class="person-title">President</p>
  <div class="divider"></div>

  <p class="contact-line contact-line--phone">
    <svg viewBox="0 0 24 24" aria-hidden="true"><path fill="#e8322f" d="M6.6 10.8a15.1 15.1 0 0 0 6.6 6.6l2.2-2.2a1 1 0 0 1 1-.25 11.4 11.4 0 0 0 3.6.57 1 1 0 0 1 1 1V20a1 1 0 0 1-1 1A17 17 0 0 1 3 4a1 1 0 0 1 1-1h3.5a1 1 0 0 1 1 1c0 1.25.2 2.45.57 3.6a1 1 0 0 1-.25 1z"/></svg>
    (555)-014-2286
  </p>
  <p class="contact-line contact-line--email">
    <svg viewBox="0 0 24 24" aria-hidden="true"><rect x="2" y="5" width="20" height="14" rx="1.5" fill="#e8322f"/><path d="M3 6l9 7 9-7" fill="none" stroke="#fff" stroke-width="1.8"/></svg>
    pdunmore@quillpost-mail.net
  </p>

  <div class="corner-accent"></div>
</section>

</body>
</html>
```